Human Resource Consulting practice needs a business card design

We need a business card design (double sided colour) for our Human Resource (HR) consulting practice in regional New South Wales, australia. Our business name is Staff Compass. We support small and medium business across the Mid North Coast of New South Wales by providing them with outsourced HR support, services and products to help them achieve compliance with workplace legislation and across all areas of the employment lifecycle from recruitment to termination and everything in between. Our corporate colours are hot pink and black. The final design should communicate professionalism, trust, people focus.
I have attached the current (old) business card for your reference.

Target Market(s)

Business owners and high level managers

Industry/Entity Type

Business

Contact Information for Business Card

Name
Title
Phone no
Mobile no
Address
PO Box
email address
website

Colors
e34197

Requirements
Must have
• Tempate for changing business card personal details including Name, position title, mobile number, email address.
• Keep current logo and colours as per attached
• Logo must be presented in 2 colours or black only not white
Nice to have
• One side logo and graphic only other side logo and personal details
Should not have
• Should not be the same as the current version (attached) but a modern interpretation.
• Does not need a busy reverse side with our list of services as per current version. I feel this is too busy.
• No photos

```html
<!DOCTYPE html>
<html lang="en">
<head>
<meta charset="utf-8">
<title>Staff Compass – Business Card</title>
<link rel="stylesheet" href="https://fonts.googleapis.com/css2?family=Lato:wght@400;700&display=swap">
<style>
  :root {
    --hot-pink: #e34197;
    --name-pink: #c42a7c;
    --deep-pink: #b0124f;
    --ink: #2b2b2f;
    --title-grey: #c9c6c4;
    --backdrop: #e8e5e2;
  }
  * { margin: 0; padding: 0; box-sizing: border-box; }
  html, body {
    width: 1200px; height: 970px; overflow: hidden;
    background: var(--backdrop);
    font-family: "Lato", Arial, sans-serif;
  }
  .canvas { position: relative; width: 1200px; height: 970px; }
  .business-card {
    position: absolute; left: 172px; top: 270px;
    width: 855px; height: 475px;
    border-radius: 22px; overflow: hidden;
    box-shadow: 0 14px 40px rgba(0,0,0,0.18);
  }
  .card-shapes { position: absolute; inset: 0; }
  .brand-name {
    position: absolute; left: 36px; top: 92px;
    font-size: 62px; font-weight: 700; color: var(--hot-pink);
    line-height: 1; letter-spacing: -1px; white-space: nowrap;
  }
  .contact-list {
    position: absolute; left: 32px; top: 212px;
    list-style: none; font-size: 22px; color: var(--ink);
  }
  .contact-list li { display: flex; align-items: center; gap: 10px; height: 28px; }
  .contact-icon { width: 22px; height: 22px; flex: none; }
  .postal-address {
    position: absolute; left: 40px; top: 372px;
    font-size: 21px; line-height: 28px; color: var(--ink); font-style: normal;
  }
  .person { position: absolute; right: 37px; top: 210px; text-align: right; }
  .person-name { font-size: 24px; font-weight: 700; color: var(--name-pink); line-height: 30px; }
  .person-title { font-size: 21px; color: var(--title-grey); line-height: 30px; }
</style>
</head>
<body>
<main class="canvas">
  <section class="business-card">
    <svg class="card-shapes" width="855" height="475" viewBox="0 0 855 475">
      <defs>
        <linearGradient id="frostTone" x1="0" y1="0" x2="0" y2="1">
          <stop offset="0" stop-color="#f6f0f3"/>
          <stop offset="0.6" stop-color="#f2dde6"/>
          <stop offset="1" stop-color="#efd2dd"/>
        </linearGradient>
        <linearGradient id="blackPanel" x1="0" y1="0" x2="1" y2="1">
          <stop offset="0" stop-color="#2a2a2c"/>
          <stop offset="0.5" stop-color="#070708"/>
          <stop offset="1" stop-color="#161617"/>
        </linearGradient>
      </defs>
      <rect width="855" height="475" fill="url(#frostTone)" role="img" aria-label="Frosted background with a soft pattern of pale pink stars"/>
      <path d="M555,0 C470,80 418,200 438,320 C448,390 478,440 498,475 L855,475 L855,0 Z" fill="var(--deep-pink)"/>
      <path d="M602,0 C505,90 452,210 462,320 C470,390 490,440 506,475 L855,475 L855,0 Z" fill="url(#blackPanel)"/>
    </svg>

    <p class="brand-name">Staff Compass</p>

    <ul class="contact-list">
      <li>
        <svg class="contact-icon" viewBox="0 0 24 24"><path d="M3 9c0-3 4-5 9-5s9 2 9 5v2h-5V9H8v2H3z M6 13h12l2 7H4z" fill="var(--hot-pink)"/><circle cx="12" cy="16.5" r="2" fill="#fff"/></svg>
        <span>02 6500 1234</span>
      </li>
      <li>
        <svg class="contact-icon" viewBox="0 0 24 24"><rect x="6" y="2" width="12" height="20" rx="2" fill="var(--hot-pink)"/><rect x="8" y="5" width="8" height="12" fill="#fff"/><circle cx="12" cy="19.3" r="1.1" fill="#fff"/></svg>
        <span>0400 555 218</span>
      </li>
      <li>
        <svg class="contact-icon" viewBox="0 0 24 24"><rect x="2" y="5" width="20" height="14" rx="1" fill="var(--hot-pink)"/><path d="M3 6l9 7 9-7" fill="none" stroke="#fff" stroke-width="1.6"/></svg>
        <span>claire@staffcompass.com.au</span>
      </li>
      <li>
        <svg class="contact-icon" viewBox="0 0 24 24"><circle cx="12" cy="12" r="10" fill="var(--hot-pink)"/><g fill="none" stroke="#fff" stroke-width="1.3"><ellipse cx="12" cy="12" rx="4" ry="10"/><path d="M2 12h20M4 7h16M4 17h16"/></g></svg>
        <span>www.staffcompass.com.au</span>
      </li>
    </ul>

    <address class="postal-address">P.O. Box 318,<br>Kendall Bay<br>NSW 2439</address>

    <div class="person">
      <p class="person-name">Claire Bennet</p>
      <p class="person-title">Principal Consultant</p>
    </div>
  </section>
</main>
</body>
</html>
```